Flyer Design Project

A beauty salon Velmira Spa needs a flyer design to promote some new services that are available in the salon. These are anti-aging, slimming and other treatments performed on the modern high-tech cosmetological equipment.
The flyer will be distrubuted in hi-end supermarket located near the salon. It would go inside the bags when the purchases are packed at the cashier desk.
The main idea is make people read it and not to throw it away immediately. The flyer will be printed on the top quality paper.
There will either be a discound or a promotional treatment in the flyer.
We are not sure about the size of the flyer. It should not be too big neither too small. Ideally on the one side there should be information about Facial Treatments and on the other about the Body Treatments. However we are open for other suggestions of the Pixel Forum.
This is our web-site www.velmira-spa.ru
Though being in Russian, it may give you an idea of our concept.
Updates

Thanks for all the designs submitted.

One general comment would be - the flyer should look different from the usual flyer one might get regarding the beauty salon services. Please make it attractive and unusual. Thanks.

Target Market(s)

Ladies from 25 to 60 years old who are well-to-do

Industry/Entity Type

Beauty Salon

Requirements
Nice to have
• It would be nice to have some technical features in the design.
Should not have
• The flyer should not be overloaded with pictures or graphic design features. It should be elegant and clear. The design should not look too "spa" as we promote technological treatments not massages.

```html
<!DOCTYPE html>
<html lang="en">
<head>
<meta charset="utf-8">
<title>Velmira Spa — Facials 20% Off</title>
<link rel="stylesheet" href="https://fonts.googleapis.com/css2?family=Comfortaa:wght@400;700&display=swap">
<style>
  :root {
    --frame-top: #4a1c1c;
    --frame-bottom: #c7862f;
    --wine: #6b2626;
    --wine-deep: #551c1c;
    --wine-light: #7a2e2e;
    --ink: #ffffff;
    --ink-soft: #f1e6e6;
  }
  * { margin: 0; padding: 0; box-sizing: border-box; }
  html, body {
    width: 781px;
    height: 1200px;
    overflow: hidden;
    background: #ffffff;
  }
  .flyer {
    position: relative;
    width: 781px;
    height: 1200px;
    padding: 10px;
    background: linear-gradient(180deg, var(--frame-top) 0%, #6a2a22 55%, var(--frame-bottom) 100%);
    font-family: "Comfortaa", sans-serif;
    color: var(--ink);
  }
  .panel {
    position: relative;
    width: 100%;
    height: 100%;
    overflow: hidden;
    background: var(--wine);
  }
  .damask-field {
    position: absolute;
    inset: 0;
    background: radial-gradient(ellipse at 50% 40%, var(--wine-light) 0%, var(--wine) 55%, var(--wine-deep) 100%);
  }
  .content {
    position: relative;
    height: 100%;
    text-align: center;
  }
  .title {
    position: absolute;
    top: 58px;
    left: 0; right: 0;
    font-size: 132px;
    font-weight: 400;
    letter-spacing: 2px;
    line-height: 1;
  }
  .services {
    position: absolute;
    top: 220px;
    left: 0; right: 0;
    font-size: 48px;
    line-height: 66px;
    font-weight: 400;
    color: var(--ink);
  }
  .offer {
    position: absolute;
    top: 480px;
    left: 0; right: 0;
    font-size: 150px;
    line-height: 122px;
    font-weight: 400;
  }
  .brand-name {
    position: absolute;
    top: 1030px;
    left: 0; right: 0;
    font-size: 46px;
    font-weight: 400;
    line-height: 1;
    color: var(--ink);
  }
  .brand-tag {
    position: absolute;
    top: 1090px;
    left: 0; right: 0;
    font-size: 22px;
    line-height: 1;
    letter-spacing: 3px;
    color: var(--ink-soft);
  }
  .website {
    position: absolute;
    top: 1138px;
    left: 0; right: 0;
    font-size: 25px;
    line-height: 1;
    color: var(--ink-soft);
  }
</style>
</head>
<body>
  <div class="flyer">
    <div class="panel">
      <div class="damask-field" role="img" aria-label="Subtle dark wine damask scroll pattern background"></div>
      <div class="content">
        <h1 class="title">facials</h1>
        <p class="services">cosmetology<br>anti ageing</p>
        <p class="offer">20%<br>OFF</p>
        <p class="brand-name">Velmira Spa</p>
        <p class="brand-tag">салон красоты</p>
        <p class="website">www.velmira-spa.ru</p>
      </div>
    </div>
  </div>
</body>
</html>
```